KRT Info Brochure

We need a brochure design for a new not-for-profit organisation that is aimed at providing homeless people with a residence that also provides counselling and vocational training to assist them to find suitable employment at the end of the program.
PLEASE NOTE:
Brochure to be A4.
I know the brochure is quite long, it is really a booklet, but please note that it does not have to have a lot of work done on it, I just want it to look professional and the front cover and inside page to look good.
Also please leave about 2-3 pages at the end as I will be adding in some architect drawings.
Please add in a last page with Contact written at the bottom - we will fill that in later. So please ensure it is editable in PDF.
Thank you so much.
Cheers
Marta

```html
<!DOCTYPE html>
<html lang="en">
<head>
<meta charset="utf-8">
<title>KRT Info Brochure – Contents and Executive Summary</title>
<link href="https://fonts.googleapis.com/css2?family=Arimo:wght@400;700&display=swap" rel="stylesheet">
<style>
  :root {
    --bg: #d9d9d9;
    --paper: #ffffff;
    --paper-shade: #eef0f2;
    --olive: #8a8731;
    --gold: #f3b433;
    --gold-pale: #f8d98a;
    --ink: #333333;
    --ink-soft: #555555;
    --heading: #8f8d2a;
    --photo-a: #c7b8a4;
    --photo-b: #7d9bb8;
  }
  * { box-sizing: border-box; margin: 0; padding: 0; }
  html, body { width: 1200px; height: 847px; overflow: hidden; }
  body {
    background: var(--bg);
    font-family: "Arimo", Arial, sans-serif;
    color: var(--ink);
  }
  .spread {
    position: absolute;
    left: 63px; top: 43px;
    width: 1074px; height: 760px;
    display: flex;
    box-shadow: 0 8px 24px rgba(0,0,0,.25);
  }
  .page {
    position: relative;
    width: 537px; height: 760px;
    background: linear-gradient(90deg, var(--paper), var(--paper-shade));
    overflow: hidden;
  }
  .page--right { background: linear-gradient(90deg, var(--paper-shade), var(--paper) 20%); }
  .band { position: absolute; left: 0; width: 537px; }
  .band--top { top: 0; height: 120px; }
  .band--bottom { bottom: 0; height: 130px; }

  .contents {
    position: absolute;
    left: 40px; top: 150px; width: 400px;
    font-size: 8.3px; line-height: 9.55px;
  }
  .contents__title { font-weight: 700; font-size: 9px; margin-bottom: 1px; }
  .contents__list { list-style: none; }
  .toc-row { display: flex; white-space: nowrap; }
  .toc-row .num { display: inline-block; width: 26px; }
  .toc-row--sub { padding-left: 22px; }
  .toc-row .leader {
    flex: 1;
    border-bottom: 1px dotted var(--ink-soft);
    margin: 0 2px 2px;
  }

  .summary {
    position: absolute;
    left: 38px; top: 118px; width: 455px;
    font-size: 8.6px; line-height: 11px;
  }
  .summary__title {
    color: var(--heading);
    font-size: 15px; font-weight: 700;
    margin-bottom: 2px;
  }
  .summary p { margin-bottom: 10px; }
  .summary .definitions { width: 220px; }

  .brand {
    position: absolute;
    left: 100px; top: 478px;
    color: var(--heading);
    font-size: 22px; font-weight: 700; line-height: 24px;
  }
  .photo {
    position: absolute;
    left: 270px; top: 360px;
    width: 235px; height: 200px;
    border-radius: 50% 50% 40% 40%;
    background: radial-gradient(ellipse at 50% 45%, var(--photo-a), var(--photo-b) 80%);
    opacity: .85;
  }
</style>
</head>
<body>
<main class="spread">
  <section class="page page--left" aria-label="Contents page">
    <svg class="band band--top" viewBox="0 0 537 120" preserveAspectRatio="none" aria-hidden="true">
      <path d="M0 0H537V28C420 10 300 70 160 92C90 102 40 98 0 92Z" fill="var(--olive)"/>
      <path d="M0 100C60 108 150 100 230 84C330 62 430 34 537 40" stroke="var(--gold)" stroke-width="4" fill="none"/>
      <path d="M0 106C80 112 170 102 250 86C340 68 440 46 537 48" stroke="var(--gold-pale)" stroke-width="1.5" fill="none"/>
    </svg>

    <div class="contents">
      <h2 class="contents__title">CONTENTS</h2>
      <ul class="contents__list">
        <li class="toc-row">Executive Summary<span class="leader"></span></li>
        <li class="toc-row"><span class="num">1.</span>HOMELESSNESS<span class="leader"></span></li>
        <li class="toc-row"><span class="num">2.</span>PROGRAM OVERVIEW<span class="leader"></span></li>
        <li class="toc-row"><span class="num">2.1.</span>Physiological<span class="leader"></span></li>
        <li class="toc-row"><span class="num">2.2.</span>Psychological<span class="leader"></span></li>
        <li class="toc-row"><span class="num">2.3.</span>Learning/Training<span class="leader"></span></li>
        <li class="toc-row"><span class="num">2.4.</span>Special Needs<span class="leader"></span></li>
        <li class="toc-row"><span class="num">2.5.</span>Vocational Education<span class="leader"></span></li>
        <li class="toc-row"><span class="num">2.6.</span>Fitting back into Society<span class="leader"></span></li>
        <li class="toc-row"><span class="num">2.7.</span>Outreach / After Care Program<span class="leader"></span></li>
        <li class="toc-row"><span class="num">2.8.</span>Family Groups<span class="leader"></span></li>
        <li class="toc-row"><span class="num">2.9.</span>Young People<span class="leader"></span></li>
        <li class="toc-row"><span class="num">2.10.</span>Older People<span class="leader"></span></li>
        <li class="toc-row"><span class="num">2.11.</span>Alcohol &amp; Drug Dependencies<span class="leader"></span></li>
        <li class="toc-row"><span class="num">3.</span>OPERATIONS<span class="leader"></span></li>
        <li class="toc-row"><span class="num">3.1.</span>Management<span class="leader"></span></li>
        <li class="toc-row"><span class="num">3.2.</span>Business Location<span class="leader"></span></li>
        <li class="toc-row"><span class="num">3.3.</span>Foundation Management<span class="leader"></span></li>
        <li class="toc-row"><span class="num">3.4.</span>KRT Staff<span class="leader"></span></li>
        <li class="toc-row"><span class="num">3.5.</span>Self-Sustainment<span class="leader"></span></li>
        <li class="toc-row"><span class="num">3.6.</span>Timeframes<span class="leader"></span></li>
        <li class="toc-row"><span class="num">3.7.</span>Marketing and Publicity<span class="leader"></span></li>
        <li class="toc-row"><span class="num">4.</span>THE PROGRAM PRACTICALLY<span class="leader"></span></li>
        <li class="toc-row"><span class="num">4.1.</span>Work Task<span class="leader"></span></li>
        <li class="toc-row"><span class="num">4.2.</span>Snapshot of a day in the Program<span class="leader"></span></li>
        <li class="toc-row"><span class="num">4.3.</span>Logistics<span class="leader"></span></li>
        <li class="toc-row"><span class="num">5.</span>THE FUTURE<span class="leader"></span></li>
        <li class="toc-row"><span class="num">5.1.</span>Complimentary Businesses<span class="leader"></span></li>
        <li class="toc-row toc-row--sub"><span class="num">5.1.1.</span>Phase 1<span class="leader"></span></li>
        <li class="toc-row toc-row--sub"><span class="num">5.1.2.</span>Phase 2<span class="leader"></span></li>
        <li class="toc-row toc-row--sub"><span class="num">5.1.3.</span>Phase 3<span class="leader"></span></li>
        <li class="toc-row toc-row--sub"><span class="num">5.1.4.</span>Phase 4<span class="leader"></span></li>
        <li class="toc-row toc-row--sub"><span class="num">5.1.5.</span>Phase 5<span class="leader"></span></li>
        <li class="toc-row"><span class="num">5.2.</span>The Long Term<span class="leader"></span></li>
        <li class="toc-row"><span class="num">6.</span>THE FINANCES<span class="leader"></span></li>
        <li class="toc-row"><span class="num">6.1.</span>Funding<span class="leader"></span></li>
        <li class="toc-row"><span class="num">6.2.</span>Income<span class="leader"></span></li>
        <li class="toc-row"><span class="num">6.3.</span>Fundraising<span class="leader"></span></li>
        <li class="toc-row">Attachment 1: S.W.O.T. analysis<span class="leader"></span></li>
        <li class="toc-row">Attachment 2: Learning For Residents<span class="leader"></span></li>
      </ul>
    </div>

    <svg class="band band--bottom" viewBox="0 0 537 130" preserveAspectRatio="none" aria-hidden="true">
      <path d="M0 10C120 40 260 70 380 60C450 54 500 40 537 30V130H0Z" fill="var(--olive)"/>
      <path d="M0 6C120 36 260 64 380 54C450 48 500 34 537 24" stroke="var(--gold)" stroke-width="4" fill="none"/>
    </svg>
  </section>

  <section class="page page--right" aria-label="Executive summary page">
    <svg class="band band--top" viewBox="0 0 537 120" preserveAspectRatio="none" aria-hidden="true">
      <path d="M0 0H537V40C480 50 400 44 320 36C220 26 110 40 0 80Z" fill="var(--olive)"/>
      <path d="M0 90C110 50 220 36 320 46C400 54 480 60 537 50" stroke="var(--gold)" stroke-width="4" fill="none"/>
      <path d="M0 98C120 58 230 44 330 54C410 62 480 66 537 58" stroke="var(--gold-pale)" stroke-width="1.5" fill="none"/>
    </svg>

    <article class="summary">
      <h1 class="summary__title">Executive Summary</h1>
      <p>KRT Legacy Foundation (KRT) is a not-for-profit organisation that will attempt to break the cycle of homelessness. KRT will provide a live-in residence for homeless people from all age ranges and provide psychological counselling to address the issues associated with the reasons for, and impact of homelessness.</p>
      <p>It is expected that most ‘Residents’ will require on average twelve months in residence to address their psychological issues, during this time the Resident will be also provided with various types of training, from life-skills to specific vocational education to assist them to move towards independent living.</p>
      <p>Once the Resident is ready, KRT staff will assist the Resident with all aspects of transitioning to independent living and provide on-going assistance and support for as long as is required.</p>
      <p>KRT will cater for family groups and single parents, providing counselling for the entire family group and training for the parent. During the residency the children will attend a local school to reduce the impact to their education.</p>
      <p>KRT recognises that the cost of running the facility and providing training and work experience to a reasonably large group of people in todays economic environment will be challenging. As such, KRT is seeking funding for the initial establishment of the facility, but aims to introduce a number of separate complimentary business entities that will provide the necessary training avenue and income required with the aim of eventually being self-sustaining.</p>
      <p>Overall, KRT aims to reduce the overall incidence of homelessness Australia wide.</p>
      <p class="definitions">Residents = homeless people living at KRT complex</p>
      <p class="definitions">Clients = Residents who have been through the Program and returned to independent living, but remain in the After Care program</p>
    </article>

    <div class="photo" role="img" aria-label="Photograph of a diverse group of smiling young people standing in a circle, hands joined in the centre, seen from above"></div>

    <p class="brand">KRT</p>

    <svg class="band band--bottom" viewBox="0 0 537 130" preserveAspectRatio="none" aria-hidden="true">
      <path d="M0 40C40 34 90 36 160 48C260 66 400 56 537 4V130H0Z" fill="var(--olive)"/>
      <path d="M0 34C40 28 90 30 160 42C260 60 400 50 537 -2" stroke="var(--gold)" stroke-width="4" fill="none"/>
    </svg>
  </section>
</main>
</body>
</html>
```